Church needs a street sign design

We're a small church located in Silicon Valley, California. Our website is https://www.vgtmarlowfield.org/ and our address is 4817 Ferrow Ave, San Jose, California, 95873. You can look up our location on Google Maps to see the sign from Street View. I have uploaded an image of the street sign as well. The marquee, the top section of the sign, and the separating line between them both will be removed. We're seeking a design for a new backlit acrylic insert that will go on the front of the light box and the back of the lightbox. The acrylic sign will fill the entire external frame. In the future, we may build a decorative wood frame around the structural legs, as visualized in one of the uploaded files. The church's brand colors are: #003366 (dark blue), #ff6600 (vibrant orange), #228b22 (forest green). I have also uploaded the church's logo assets. Our primary font is Montserrat and the secondary is Poppins. You can deviate from these colors/fonts if the sign is still coherent with the rest of our branding. Our branding values are mission, truth, passion, and community (please do not put those words on the sign! They are just intended to guide the look of the design). The sign dimensions are 96" by 47.5". Keep in mind that the sign will be backlit on a busy street side. It will also be positioned next to an old-looking church building. We do NOT want a sign that looks traditional, old, or antiquated. Instead, we want a modern-looking sign that pairs well with our old building while helping it look more modern too. We would also like the web address clearly visible on the sign: vgtmarlowfield.org. If you have any questions, just let me know!

```html
<!DOCTYPE html>
<html lang="en">
<head>
<meta charset="utf-8">
<title>Valley Grace Tabernacle – Street Sign Insert</title>
<link rel="stylesheet" href="https://fonts.googleapis.com/css2?family=Montserrat:wght@600;800;900&family=Poppins:wght@400;500&display=swap">
<style>
  :root {
    --backdrop: #9e9e9e;
    --ink-black: #000000;
    --sky-glow: #fff3d6;
    --sky-amber: #f0a060;
    --sky-rust: #c8603c;
    --ridge-brown: #3a2014;
    --brand-orange: #ff6600;
    --gold-light: #f4e39a;
    --gold-mid: #cdb04a;
    --gold-deep: #8c7320;
    --white: #ffffff;
  }
  * { margin: 0; padding: 0; box-sizing: border-box; }
  html, body {
    width: 1200px;
    height: 691px;
    overflow: hidden;
    background: var(--backdrop);
  }
  .sign-panel {
    position: absolute;
    left: 107px;
    top: 101px;
    width: 986px;
    height: 483px;
    background: var(--ink-black);
    overflow: hidden;
    box-shadow: 0 4px 14px rgba(0, 0, 0, 0.35);
  }
  .hero-scene {
    position: absolute;
    inset: 0;
    background:
      radial-gradient(ellipse 260px 200px at 640px 70px, var(--sky-glow) 0%, rgba(255, 220, 160, 0.6) 35%, rgba(240, 160, 96, 0) 100%),
      linear-gradient(180deg, var(--sky-rust) 0%, var(--sky-amber) 28%, #a85a38 45%, var(--ridge-brown) 58%, #120804 70%, var(--ink-black) 80%);
  }
  .church-name {
    position: absolute;
    left: 53px;
    top: 52px;
    color: var(--white);
    font-family: "Montserrat", sans-serif;
    font-weight: 600;
    line-height: 1;
  }
  .church-name .name-main {
    display: block;
    font-size: 44px;
    letter-spacing: 0.01em;
  }
  .church-name .name-sub {
    display: block;
    font-size: 17px;
    margin-top: 8px;
    letter-spacing: 0.04em;
  }
  .message {
    position: absolute;
    left: 0;
    right: 0;
    top: 196px;
    text-align: center;
  }
  .headline {
    font-family: "Montserrat", sans-serif;
    font-weight: 900;
    font-size: 70px;
    line-height: 1;
    letter-spacing: -0.005em;
    background: linear-gradient(180deg, var(--gold-light) 0%, var(--gold-mid) 45%, var(--gold-deep) 60%, var(--gold-mid) 100%);
    -webkit-background-clip: text;
    background-clip: text;
    color: transparent;
  }
  .subhead {
    margin-top: 10px;
    font-family: "Poppins", sans-serif;
    font-weight: 400;
    font-size: 52px;
    line-height: 1;
    color: var(--brand-orange);
  }
  .tagline {
    margin-top: 16px;
    font-family: "Poppins", sans-serif;
    font-weight: 400;
    font-size: 36px;
    line-height: 1;
    letter-spacing: 0.3em;
    color: var(--white);
  }
  .web-pill {
    position: absolute;
    left: 266px;
    top: 395px;
    width: 455px;
    height: 48px;
    border-radius: 12px;
    background: var(--brand-orange);
    color: var(--white);
    font-family: "Poppins", sans-serif;
    font-weight: 500;
    font-size: 28px;
    letter-spacing: 0.1em;
    display: flex;
    align-items: center;
    justify-content: center;
  }
</style>
</head>
<body>
  <main class="sign-panel">
    <div class="hero-scene" role="img" aria-label="Sunset sky with rays of light behind a cross standing on a dark mountain ridge"></div>

    <div class="church-name">
      <span class="name-main">VALLEY GRACE</span>
      <span class="name-sub">TABERNACLE</span>
    </div>

    <div class="message">
      <h1 class="headline">MAKING DISCIPLES</h1>
      <p class="subhead">&amp; HELPING THE HELPLESS</p>
      <p class="tagline">For the Glory of Christ</p>
    </div>

    <div class="web-pill">www.vgtmarlowfield.org</div>
  </main>
</body>
</html>
```